Design 4 pages for an event discovery website

This is a contest for the design of 4 pages for an events discovery website. The feature is part of the new sign-up process.

Please see the attached document for a full scope, mockups and the parent category icons.

Target Market(s)

18-35 Australian event goers

Industry/Entity Type

Events

Number of Pages Required

4 page

```html
<!DOCTYPE html>
<html lang="en">
<head>
<meta charset="utf-8">
<title>Eventara – Sign Up Step 1</title>
<link rel="stylesheet" href="https://fonts.googleapis.com/css2?family=Arvo:wght@400;700&family=Open+Sans:ital,wght@0,400;0,600;1,400&family=Montserrat:wght@400&display=swap">
<style>
  :root {
    --orange: #f08a16;
    --ink: #333333;
    --body: #4a4a4a;
    --muted: #666666;
    --page: #f0f0f0;
    --header: #ffffff;
    --footer: #121212;
    --search: #e8e8e8;
    --login-border: #9a9a9a;
    --chirper: #5cc8ef;
    --snapgram: #b1a08a;
    --tunewave: #7ec31b;
    --melodix: #4390dc;
  }
  * { box-sizing: border-box; margin: 0; padding: 0; }
  html, body { width: 1200px; height: 711px; overflow: hidden; }
  body {
    position: relative;
    background: var(--page);
    font-family: "Open Sans", Arial, sans-serif;
    color: var(--body);
  }
  .site-header {
    position: absolute; top: 0; left: 0; width: 1200px; height: 92px;
    background: var(--header);
    box-shadow: 0 1px 4px rgba(0,0,0,0.12);
  }
  .brand {
    position: absolute; left: 131px; top: 27px;
    font-family: "Open Sans", Arial, sans-serif; font-weight: 600;
    font-size: 31px; color: var(--orange); letter-spacing: 0.5px;
  }
  .nav-link {
    position: absolute; left: 292px; top: 44px;
    font-size: 13px; color: #444;
  }
  .search {
    position: absolute; left: 656px; top: 36px; width: 226px; height: 31px;
    background: var(--search);
  }
  .search span {
    position: absolute; left: 18px; top: 8px;
    font-size: 12px; font-style: italic; color: #a5a5a5;
  }
  .search svg { position: absolute; right: 16px; top: 9px; }
  .btn-outline {
    position: absolute; top: 36px; width: 80px; height: 31px;
    border: 2px solid; font-size: 13px; text-align: center; line-height: 27px;
  }
  .btn-signup { left: 897px; border-color: var(--orange); color: var(--orange); }
  .btn-login { left: 989px; border-color: var(--login-border); color: #666; }

  .step-title {
    position: absolute; left: 134px; top: 157px;
    font-family: "Arvo", Georgia, serif; font-weight: 400;
    font-size: 25px; color: var(--ink);
  }
  .benefits { position: absolute; left: 134px; top: 211px; list-style: none; }
  .benefits li {
    position: relative; height: 37px; padding-left: 29px;
    font-size: 14.5px; line-height: 22px; color: var(--body);
  }
  .benefits svg { position: absolute; left: 0; top: 3px; }

  .service {
    position: absolute; left: 141px; width: 192px; height: 37px;
    color: #fff; font-family: "Montserrat", Arial, sans-serif;
    font-size: 13.5px; letter-spacing: 0.3px; text-transform: uppercase;
    line-height: 35px; text-align: center; padding-left: 24px;
    border-bottom: 2px solid rgba(0,0,0,0.18);
  }
  .service::before {
    content: ""; position: absolute; left: 19px; top: 11px;
    width: 13px; height: 13px; border-radius: 50%; background: #fff;
  }
  .service-chirper { top: 345px; background: var(--chirper); }
  .service-snapgram { top: 399px; background: var(--snapgram); }
  .service-tunewave { top: 452px; background: var(--tunewave); }
  .service-melodix { top: 505px; background: var(--melodix); }
  .service-note {
    position: absolute; left: 352px; font-size: 13px; line-height: 20px; color: var(--muted);
  }
  .note-linked { top: 355px; }
  .note-pending { top: 450px; width: 330px; }

  .site-footer {
    position: absolute; left: 0; top: 611px; width: 1200px; height: 100px;
    background: var(--footer);
  }
  .site-footer p {
    position: absolute; top: 46px; width: 100%; text-align: center;
    font-size: 13px; color: #e6e6e6;
  }
</style>
</head>
<body>
  <header class="site-header">
    <div class="brand">Eventara</div>
    <a class="nav-link">Find Events</a>
    <div class="search">
      <span>Search here..</span>
      <svg width="13" height="13" viewBox="0 0 13 13" aria-hidden="true">
        <circle cx="5.3" cy="5.3" r="3.8" fill="none" stroke="#555" stroke-width="1.8"/>
        <line x1="8" y1="8" x2="11.5" y2="11.5" stroke="#555" stroke-width="2" stroke-linecap="round"/>
      </svg>
    </div>
    <div class="btn-outline btn-signup">Sign Up</div>
    <div class="btn-outline btn-login">Login</div>
  </header>

  <main>
    <h1 class="step-title">STEP 1 of 5</h1>
    <ul class="benefits">
      <li><svg width="16" height="16" viewBox="0 0 16 16" aria-hidden="true"><circle cx="8" cy="8" r="6.5" fill="none" stroke="#f08a16" stroke-width="2"/><path d="M4.5 8h6M8 5.2 10.8 8 8 10.8" fill="none" stroke="#f08a16" stroke-width="2"/></svg>Link in all your other social media account and music players</li>
      <li><svg width="16" height="16" viewBox="0 0 16 16" aria-hidden="true"><circle cx="8" cy="8" r="6.5" fill="none" stroke="#f08a16" stroke-width="2"/><path d="M4.5 8h6M8 5.2 10.8 8 8 10.8" fill="none" stroke="#f08a16" stroke-width="2"/></svg>By linking your account, we can save you a lot of time</li>
      <li><svg width="16" height="16" viewBox="0 0 16 16" aria-hidden="true"><circle cx="8" cy="8" r="6.5" fill="none" stroke="#f08a16" stroke-width="2"/><path d="M4.5 8h6M8 5.2 10.8 8 8 10.8" fill="none" stroke="#f08a16" stroke-width="2"/></svg>By automatically deteriming your interests</li>
    </ul>

    <div class="service service-chirper">Chirper</div>
    <p class="service-note note-linked">linked</p>
    <div class="service service-snapgram">Snapgram</div>
    <div class="service service-tunewave">Tunewave</div>
    <p class="service-note note-pending">We don't have that features yet but have restarted your interest.</p>
    <div class="service service-melodix">Melodix</div>
  </main>

  <footer class="site-footer">
    <p>Copyright (c)2015, Yoursite, All Right Reserved.</p>
  </footer>
</body>
</html>
```